RWT Fittings Ltd Business Cards

We need a business card with our business logo. We provide window and door installations on high-rises in west coast British Colombia, Canada.

I would like my business information and details on one side of the card, and the other side the company name with logo

Target Market(s)

General Contractors

Industry/Entity Type

Construction

Contact Information for Business Card

one side i want my company name and logo in the dark theme logo that i provided

Requirements
Must have
• Marco Peltieri, 16045518293, RWTFittings@mailbox-demo.com, 1407-5194 Linden Row Burnaby BC, V5H 2K9, Owner & Manager

```html
<!DOCTYPE html>
<html lang="en">
<head>
<meta charset="utf-8">
<title>RWT Fittings Ltd – Business Cards</title>
<link href="https://fonts.googleapis.com/css2?family=Roboto:wght@400;500;700&display=swap" rel="stylesheet">
<style>
  :root {
    --backdrop: #222223;
    --card: #1f2024;
    --card-shade: #26272c;
    --accent: #27a9e1;
    --silver: #a9a9ab;
    --ink: #f2f2f2;
    --emboss: #3b3c42;
  }
  * { box-sizing: border-box; margin: 0; padding: 0; }
  html, body {
    width: 1200px; height: 780px; overflow: hidden;
    background: var(--backdrop);
    font-family: "Roboto", Arial, sans-serif;
  }
  .sheet {
    position: relative; width: 1200px; height: 780px;
    display: flex; align-items: center; justify-content: center; gap: 40px;
  }
  .card {
    position: relative; width: 540px; height: 309px;
    background: var(--card);
    box-shadow: 0 18px 40px rgba(0,0,0,.55);
    overflow: hidden;
  }
  /* contact side */
  .card--contact .shade {
    position: absolute; right: 0; bottom: 0; width: 300px; height: 200px;
    background: linear-gradient(135deg, transparent 0 40%, var(--card-shade) 40% 100%);
  }
  .brand {
    position: absolute; left: 30px; top: 30px;
    display: flex; align-items: center; gap: 10px;
  }
  .brand__mark { width: 18px; height: 18px; background: var(--accent); }
  .brand__name {
    font-weight: 500; font-size: 24px; color: var(--accent); letter-spacing: .5px;
  }
  .details {
    position: absolute; right: 52px; bottom: 30px; text-align: right;
  }
  .person { font-weight: 700; font-size: 30px; line-height: 1; }
  .person__first { color: var(--accent); }
  .person__last { color: var(--silver); }
  .role { font-weight: 500; font-size: 14px; color: var(--ink); margin: 6px 0 12px; }
  .line {
    font-size: 13px; color: var(--ink); line-height: 1.45;
    display: flex; justify-content: flex-end; align-items: center; gap: 8px;
  }
  .line svg { width: 13px; height: 13px; fill: var(--accent); }
  .accent-bar {
    position: absolute; right: 0; bottom: 40px; width: 22px; height: 70px;
    background: var(--accent);
  }
  /* logo side */
  .card--logo { display: flex; align-items: center; justify-content: center; }
  .card--logo .brand {
    position: static; gap: 16px;
  }
  .card--logo .brand__mark { width: 34px; height: 34px; background: var(--emboss); }
  .card--logo .brand__name { font-size: 44px; color: var(--emboss); }
</style>
</head>
<body>
<main class="sheet">
  <section class="card card--contact" aria-label="Business card, contact side">
    <div class="shade"></div>
    <div class="brand">
      <span class="brand__mark"></span>
      <span class="brand__name">RWT Fittings Ltd</span>
    </div>
    <div class="details">
      <p class="person"><span class="person__first">Marco</span> <span class="person__last">Peltieri</span></p>
      <p class="role">Owner &amp; Manager</p>
      <p class="line">1407-5194 Linden Row</p>
      <p class="line">Burnaby BC, V5H 2K9</p>
      <p class="line">1604 551 8293
        <svg viewBox="0 0 24 24" aria-hidden="true"><path d="M6.6 10.8a15.1 15.1 0 0 0 6.6 6.6l2.2-2.2a1 1 0 0 1 1-.25 11.4 11.4 0 0 0 3.6.57 1 1 0 0 1 1 1V20a1 1 0 0 1-1 1A17 17 0 0 1 3 4a1 1 0 0 1 1-1h3.5a1 1 0 0 1 1 1c0 1.25.2 2.45.57 3.57a1 1 0 0 1-.25 1z"/></svg>
      </p>
      <p class="line">RWTFittings@mailbox-demo.com
        <svg viewBox="0 0 24 24" aria-hidden="true"><path d="M2 5h20v14H2zm2 2v.5l8 5 8-5V7zm0 2.9V17h16V9.9l-8 5z"/></svg>
      </p>
    </div>
    <div class="accent-bar"></div>
  </section>

  <section class="card card--logo" aria-label="Business card, company side">
    <div class="brand">
      <span class="brand__mark"></span>
      <span class="brand__name">RWT Fittings Ltd</span>
    </div>
  </section>
</main>
</body>
</html>
```